Migration and redesign of existing website to WordPress using DIVI 3

I. TASK OBJECTIVE:
- Redesign our existing website www.kelvaleheelcare.com.au with a fresh new look and migrate to new Wordpress site based on DIVI3 theme. The site will contain the same basic functionality as the existing site (with some small changes).

II. STYLE/ DESIGN ASPECT:
As an example of a site that I like the look of, see https://pebblequarn.com/. I like the use of shadows, and this would go well with the little animations you can do with Divi (e.g. when hovering over pics).

1. What I am looking for is a design which has lots of white space, is modern and friendly looking (but still not too cute or frivolous, as we are a medical practice)
2. DESIGN that is NOT TOO rectangular or blocky.
3. Please take into consideration our Users are Older market, so any icons or navigation features need to be very easy to understand and not too small.
4. Must be easy to navigate
5. We are are happy to go with a new colour scheme, and are working on some ideas for this, but happy to take suggestions.

III. SPECIFICATIONS:
1. 5+ Pages (should flow like the current site)
2. Using Wordpress Divi 3 theme.
3. I'd like every page to have a "book now" button and a contact form in a sidebar so that users can click the button or fill in the contact form without scrolling at all. EXCEPT ON THE HOME PAGE, where there should still be a book now button (maybe on the top right in the header of all pages?), and maybe a contact us button which scrolls down to the contact area at the bottom of the HOME page. I don't think a side bar is necessarily required on the home page, but if you think it makes sense from a design perspective please let me know.
4. AT THE BOTTOM OF THE PAGE, just above the FOOTER, I'd like a row of trust logos for various organisations that we are affiliated with. (A list of this company will be provided later but you could temporarily use placeholders)

Once we have a structure in place, we can migrate most of the content. Please let me know if I'm not being clear or you need further information.

Podiatry Customers and Referrors

Health Care

5+ page

• Simple to navigate.
• Contact/booking details on most if not all pages - please see specification above
• Section for Trusted Affiliates above the footer
• Wordpress using Divi3 Theme
• Not too busy with the design. Plenty of white space or light background.
• Should not be complicated to navigate.
• TOO rectangular or blocky designs

```html
<!DOCTYPE html>
<html lang="en">
<head>
<meta charset="utf-8">
<title>Kelvale Heel Care Clinic</title>
<link rel="stylesheet" href="https://fonts.googleapis.com/css2?family=Acme&family=Open+Sans:wght@400;600;700&display=swap">
<style>
:root{
  --teal:#17808b;
  --teal-dark:#0f5f69;
  --teal-deep:#0c4e58;
  --blue:#3d7fc8;
  --ink:#2b2b2b;
  --muted:#777;
  --light:#eef3f4;
  --badge:#d9e3e5;
  --white:#fff;
}
*{box-sizing:border-box;margin:0;padding:0}
html,body{width:1200px;height:4225px;overflow:hidden}
body{position:relative;font-family:"Open Sans",sans-serif;color:var(--ink);background:var(--white)}
.abs{position:absolute}
h1,h2,h3,.display{font-family:"Acme",sans-serif;font-weight:400}

/* header */
.site-header{position:absolute;top:0;left:0;width:1200px;height:135px;background:var(--white)}
.brand{left:140px;top:28px;display:flex;align-items:center;gap:12px}
.brand-mark{width:40px;height:40px;border-radius:50%;background:var(--teal)}
.brand-name{font-family:"Acme",sans-serif;font-size:21px;color:var(--teal-dark)}
.call{right:140px;top:30px;display:flex;align-items:center;gap:10px;font-family:"Acme",sans-serif;font-size:22px;color:var(--teal-dark)}
.social{display:flex;gap:8px}
.social span{width:32px;height:32px;border-radius:50%;border:2px solid var(--blue);display:block}
.main-nav{left:355px;top:84px;display:flex;gap:28px;font-size:13.5px;color:#444}
.main-nav .active{color:var(--teal);border-bottom:2px solid var(--teal);padding-bottom:4px}

/* hero */
.hero{top:135px;left:0;width:1200px;height:560px}
.hero-photo{position:absolute;inset:0;background:linear-gradient(120deg,#c9b5a5 0%,#e9e4e0 35%,#9fb1c6 60%,#d8cfc8 100%)}
.hero h1{position:absolute;top:180px;width:100%;text-align:center;color:var(--white);font-size:50px;line-height:1.2;text-shadow:0 2px 6px rgba(0,0,0,.35)}
.btn{display:inline-flex;align-items:center;gap:8px;background:var(--teal-dark);color:var(--white);font-size:14px;font-weight:700;border-radius:30px;padding:12px 26px;text-transform:uppercase}
.hero .btn{position:absolute;top:325px;left:517px}
.hero-arrow{position:absolute;top:260px;width:14px;height:14px;border-left:2px solid #fff;border-bottom:2px solid #fff}
.hero-curve{position:absolute;left:0;bottom:0}

/* practice */
.section-title{position:absolute;width:1200px;text-align:center;font-size:36px;color:#333}
.practice-intro{top:758px;left:200px;width:800px;text-align:center;font-size:13px;color:var(--muted);line-height:1.7}
.practice-cards{top:830px;left:100px;width:1000px;height:310px}
.card{position:absolute;top:0;width:250px;height:310px;text-align:center;color:var(--white);padding-top:58px}
.card .icon{width:74px;height:74px;margin:0 auto 18px;border-radius:16px;background:rgba(255,255,255,.9)}
.card h3{font-family:"Open Sans",sans-serif;font-weight:600;font-size:19px;margin-bottom:10px}
.card p{font-size:11.5px;line-height:1.6;padding:0 36px}
.card .more{display:inline-block;margin-top:12px;font-size:11px;font-weight:700}

/* team */
.team{top:1230px;left:0;width:1200px;height:530px;background:linear-gradient(90deg,var(--teal-deep),var(--teal) 55%,#3a9aa4)}
.team .section-title{top:82px;color:var(--white)}
.member{position:absolute;top:170px;width:210px;text-align:center}
.avatar{width:200px;height:200px;margin:0 auto 22px;border-radius:50%;border:6px solid var(--white);background:linear-gradient(160deg,#e7dbd2,#b9c7cf)}
.member h3{font-family:"Acme",sans-serif;font-size:22px;color:#1a1a1a}
.member p{font-size:15px;color:#1a1a1a}
.slide-arrow{position:absolute;top:290px;width:20px;height:20px;border-left:2px solid #fff;border-bottom:2px solid #fff}

/* about */
.about-photo{background:linear-gradient(135deg,#3a3f4a,#a3784f 55%,#e58a3d)}
.about-photo.two{background:linear-gradient(135deg,#f1ece8,#d9d4cf 50%,#9aa9b3)}
.about h2{font-family:"Open Sans",sans-serif;font-weight:600;font-size:22px;line-height:1.4;color:#222}
.about p{font-size:12.5px;line-height:1.9;color:var(--muted)}
.about .link{color:var(--teal);font-size:12px}

/* book */
.free-book{top:2550px;left:0;width:1200px;height:550px;background:var(--light)}
.book-circle{position:absolute;left:125px;top:70px;width:420px;height:420px;border-radius:50%;background:#d2e4e6}
.book-cover{position:absolute;left:225px;top:120px;width:218px;height:316px;background:linear-gradient(180deg,#2e6fb3 0 38%,#7a9ab8 38%,#4c6a88 100%);box-shadow:0 6px 18px rgba(0,0,0,.25);padding:14px 12px;color:#fff}
.book-cover strong{display:block;font-size:20px;font-weight:700}
.book-cover small{display:block;font-size:8px;line-height:1.5;margin-top:6px}
.free-book .kicker{left:565px;top:150px;font-size:36px;color:var(--teal)}
.free-book h3{left:565px;top:210px;font-family:"Open Sans",sans-serif;font-weight:600;font-size:22px;line-height:1.45;color:#222}
.free-book p{left:565px;top:290px;width:520px;font-size:12.5px;line-height:1.8;color:var(--muted)}
.free-book .btn{left:565px;top:355px;font-size:13px;text-transform:none;padding:10px 24px}

/* cases */
.case{position:absolute;top:3228px;width:327px;height:170px;border-radius:4px;background:linear-gradient(135deg,#1f8893,#2f99a2);border:3px solid #bfe1e4;color:#fff;text-align:center;padding-top:56px;box-shadow:0 4px 12px rgba(0,0,0,.15)}
.case h3{font-family:"Acme",sans-serif;font-size:22px}
.case span{display:block;font-size:11px;margin-top:8px}
.cases-btn{position:absolute;top:3412px;left:490px;font-size:13px;text-transform:none;padding:10px 24px}

/* affiliates */
.affiliates{top:3462px;left:300px;width:600px;display:flex;justify-content:space-between}
.affiliates span{width:96px;height:34px;border-radius:17px;background:var(--badge);display:block}

/* footer */
.site-footer{top:3520px;left:0;width:1200px;height:705px;background:linear-gradient(180deg,#2e2b2a,#231f1f)}
.footer-curve{position:absolute;top:-2px;left:0}
.contact h2{left:100px;top:140px;font-size:30px;color:#fff}
.contact p{left:100px;top:190px;width:360px;font-size:12px;line-height:1.7;color:#ddd}
.field{position:absolute;left:100px;width:350px;height:42px;background:#fff;border-radius:2px;font-size:12px;color:#888;padding:12px 10px}
.submit{position:absolute;left:100px;top:513px;width:196px;height:44px;background:var(--teal-dark);color:#fff;font-size:13px;font-weight:700;text-align:center;line-height:44px}
.divider{left:520px;top:260px;width:1px;height:240px;background:#555}
.address-col h3{left:586px;top:208px;font-size:24px;color:#fff}
.info-row{position:absolute;left:586px;display:flex;align-items:flex-start;gap:18px;color:#ddd;font-size:12px;line-height:1.7}
.info-row .bubble{width:42px;height:42px;border-radius:50%;background:#fff;flex:none;display:flex;align-items:center;justify-content:center}
.footer-brand{left:860px;top:360px;display:flex;align-items:center;gap:10px;font-family:"Acme",sans-serif;font-size:24px;color:#4fb3bd}
.footer-brand span.mark{width:40px;height:40px;border-radius:50%;background:#4fb3bd}
.connect{left:586px;top:485px;display:flex;align-items:center;gap:16px;font-family:"Acme",sans-serif;font-size:24px;color:#fff}
.connect .social span{border-color:#fff;width:34px;height:34px}
.rule{left:100px;top:627px;width:1000px;height:1px;background:#555}
.copyright{top:662px;width:1200px;text-align:center;font-size:12px;color:#ccc}
</style>
</head>
<body>

<header class="site-header">
  <div class="abs brand"><span class="brand-mark"></span><span class="brand-name">Kelvale Heel Care Clinic</span></div>
  <div class="abs call">
    <svg width="20" height="20" viewBox="0 0 24 24" aria-hidden="true"><path fill="#0f5f69" d="M6.6 10.8a15 15 0 0 0 6.6 6.6l2.2-2.2c.3-.3.7-.4 1-.2 1.1.4 2.3.6 3.6.6.6 0 1 .4 1 1V20c0 .6-.4 1-1 1A17 17 0 0 1 3 4c0-.6.4-1 1-1h3.5c.6 0 1 .4 1 1 0 1.3.2 2.5.6 3.6.1.3 0 .7-.2 1z"/></svg>
    Call Us Today ! (08) 5550 1842
    <div class="social"><span></span><span></span><span></span><span></span></div>
  </div>
  <nav class="abs main-nav">
    <span class="active">Home</span><span>Common Problems ⌄</span><span>Services ⌄</span><span>About Us ⌄</span><span>Case Histories</span><span>Helpful Information ⌄</span><span>Blog</span><span>Contact</span>
  </nav>
</header>

<section class="abs hero">
  <div class="hero-photo" role="img" aria-label="Podiatrist examining a patient's foot on a treatment table"></div>
  <h1>We Offer Solutions To Common<br>Foot Problems</h1>
  <span class="btn">
    <svg width="14" height="14" viewBox="0 0 24 24" aria-hidden="true"><circle cx="12" cy="12" r="11" fill="#fff"/><path d="M10 7l5 5-5 5" stroke="#0f5f69" stroke-width="2.5" fill="none"/></svg>
    Book Now</span>
  <i class="hero-arrow" style="left:40px;transform:rotate(45deg)"></i>
  <i class="hero-arrow" style="right:40px;transform:rotate(-135deg)"></i>
  <svg class="hero-curve" width="1200" height="70" viewBox="0 0 1200 70" aria-hidden="true">
    <path d="M0 20 Q600 80 1200 20 V70 H0z" fill="#fff"/>
    <path d="M0 20 Q600 80 1200 20" stroke="var(--teal)" stroke-width="6" fill="none"/>
  </svg>
</section>

<h2 class="section-title" style="top:700px">Practice Areas</h2>
<p class="abs practice-intro">When you suffer from a foot or ankle problem, the pain and discomfort can make it a challenge to engage in simple, daily activities. When the pain disrupts your life, you need to contact a skilled, experienced podiatrist to get resolution.</p>

<div class="abs practice-cards">
  <svg class="abs" width="1000" height="310" viewBox="0 0 1000 310" aria-hidden="true">
    <polygon points="0,0 250,0 270,155 250,310 0,310" fill="#3f82cb"/>
    <polygon points="250,0 500,0 520,155 500,310 250,310 270,155" fill="#3a7cc5"/>
    <polygon points="500,0 750,0 770,155 750,310 500,310 520,155" fill="#3f82cb"/>
    <polygon points="750,0 1000,0 1000,310 750,310 770,155" fill="#3a7cc5"/>
  </svg>
  <div class="card" style="left:0"><div class="icon" role="img" aria-label="Foot icon"></div><h3>Common Problems</h3><p>Foot, toe or ankle pain can be severe and it can interfere with your ability</p><span class="more">Read More ›</span></div>
  <div class="card" style="left:250px"><div class="icon" role="img" aria-label="Foot bones icon"></div><h3>Foot &amp; Ankle Surgery</h3><p>Foot and ankle pain can be extremely distracting and uncomfortable</p><span class="more">Read More ›</span></div>
  <div class="card" style="left:500px"><div class="icon" role="img" aria-label="Dancer's foot icon"></div><h3>Sport and Dance</h3><p>Foot and ankle pain can be extremely distracting and uncomfortable</p><span class="more">Read More ›</span></div>
  <div class="card" style="left:750px"><div class="icon" role="img" aria-label="Painful foot icon"></div><h3>All Our Services</h3><p>Special patient groups require intensive and constant care to keep healthy</p><span class="more">Read More ›</span></div>
</div>

<section class="abs team">
  <h2 class="section-title">Meet Our Team</h2>
  <i class="slide-arrow" style="left:72px;transform:rotate(45deg)"></i>
  <i class="slide-arrow" style="right:72px;transform:rotate(-135deg)"></i>
  <div class="member" style="left:113px"><div class="avatar" role="img" aria-label="Portrait of podiatric surgeon"></div><h3>Nora Vance</h3><p>Podiatric Surgeon</p></div>
  <div class="member" style="left:373px"><div class="avatar" role="img" aria-label="Portrait of podiatrist"></div><h3>Callum Reid</h3><p>Podiatrist</p></div>
  <div class="member" style="left:616px"><div class="avatar" role="img" aria-label="Portrait of podiatrist"></div><h3>Elise Hartley</h3><p>Podiatrist</p></div>
  <div class="member" style="left:860px"><div class="avatar" role="img" aria-label="Portrait of podiatrist"></div><h3>Jenna Corlett</h3><p>Podiatrist</p></div>
</section>

<section class="about">
  <div class="abs about-photo" style="left:105px;top:1845px;width:370px;height:295px;box-shadow:0 4px 14px rgba(0,0,0,.18)" role="img" aria-label="Runner's feet with highlighted heel pain"></div>
  <h2 class="abs" style="left:507px;top:1853px;width:540px">Let Our Kelvale Podiatrists Relieve Your Foot and Ankle Pain</h2>
  <p class="abs" style="left:507px;top:1928px;width:590px">Whether you are an office worker, pensioner or professional athlete, nearly all people will experience problems in their feet and ankles at some point in their lives. Unfortunately, a problem in the foot can affect the whole body, causing an infection to spread, deformities in the feet, and pain to travel upward into the leg. It doesn't take long before a foot injury may cause wide-ranging consequences, including lost mobility, a drain on your finances, and a decline in your physical health. Even when patients attempt to cure their conditions once and for all, they often suffer the frustration of treating the symptoms only to have the problem return in full force.</p>

  <h2 class="abs" style="left:100px;top:2200px;width:560px">A Proven Track Record of Correcting Foot Pain in Kelvale Patients</h2>
  <p class="abs" style="left:100px;top:2285px;width:590px">At the Kelvale Heel Care Clinic, we know that there are often a variety of causes of foot and ankle pain, and each must be addressed to solve your problem for good. We examine your feet, posture, and gait to identify any biomechanical issues that could be causing your pain, treat ulcerations and foot deformities that prohibit full range of motion, and perform many different surgical techniques to restore your mobility and lifestyle. Call the number on this page today to tell our podiatrists about your condition and schedule your appointment. <span class="link" style="margin-left:150px">[Read More]</span></p>
  <div class="abs about-photo two" style="left:727px;top:2178px;width:366px;height:290px;box-shadow:0 4px 14px rgba(0,0,0,.18)" role="img" aria-label="Gloved hands treating a patient's foot"></div>
</section>

<section class="abs free-book">
  <div class="book-circle"></div>
  <div class="book-cover" role="img" aria-label="Cover of the podiatric surgery book with surgical photo">
    <strong>Podiatric Surgery</strong>
    <small>Dr Nora Vance BSc, PGDip Surg<br>Kelvale Heel Care Clinic<br>14 Larkspur Road<br>Kelvale WA 6999</small>
  </div>
  <div class="abs display kicker">Free Book</div>
  <h3 class="abs">Free Foot Surgery Book by Podiatric Surgeon,<br>Dr Nora Vance</h3>
  <p class="abs">This book was created to demonstrate examples of some foot conditions that can be easily corrected by our Podiatric Surgeon, Dr Nora Vance.</p>
  <span class="abs btn">View Details
    <svg width="14" height="14" viewBox="0 0 24 24" aria-hidden="true"><circle cx="12" cy="12" r="11" fill="#fff"/><path d="M10 7l5 5-5 5" stroke="#0f5f69" stroke-width="2.5" fill="none"/></svg></span>
</section>

<h2 class="section-title" style="top:3158px">Case Histories</h2>
<div class="case" style="left:100px" role="img" aria-label="Plantar fascia treatment photo, teal tinted"><h3>Plantar fascia Case</h3><span>Read More ›</span></div>
<div class="case" style="left:437px" role="img" aria-label="Bunion treatment photo, teal tinted"><h3>Bunion Case</h3><span>Read More ›</span></div>
<div class="case" style="left:774px" role="img" aria-label="Foot trauma photo, teal tinted"><h3>Trauma case</h3><span>Read More ›</span></div>
<span class="btn cases-btn">View All Case Histories
  <svg width="14" height="14" viewBox="0 0 24 24" aria-hidden="true"><circle cx="12" cy="12" r="11" fill="#fff"/><path d="M10 7l5 5-5 5" stroke="#0f5f69" stroke-width="2.5" fill="none"/></svg></span>

<div class="abs affiliates" role="img" aria-label="Trusted affiliate badges">
  <span></span><span></span><span></span><span></span><span></span>
</div>

<footer class="abs site-footer">
  <svg class="footer-curve" width="1200" height="80" viewBox="0 0 1200 80" aria-hidden="true">
    <path d="M0 0 H1200 V10 Q600 90 0 10z" fill="#fff"/>
    <path d="M0 10 Q600 90 1200 10" stroke="var(--teal)" stroke-width="6" fill="none"/>
  </svg>
  <section class="contact">
    <h2 class="abs">Contact Us</h2>
    <p class="abs">Please fill out this quick contact form and someone will be in touch with you shortly!</p>
    <div class="field" style="top:246px">Name *</div>
    <div class="field" style="top:296px">Email *</div>
    <div class="field" style="top:346px">Phone *</div>
    <div class="field" style="top:396px;height:110px">Tell us More</div>
    <div class="submit">SUBMIT MESSAGE</div>
  </section>
  <div class="abs divider"></div>
  <section class="address-col">
    <h3 class="abs">Address :</h3>
    <div class="info-row" style="top:258px"><span class="bubble"><svg width="18" height="18" viewBox="0 0 24 24" aria-hidden="true"><path fill="#2a2828" d="M12 2a7 7 0 0 0-7 7c0 5 7 13 7 13s7-8 7-13a7 7 0 0 0-7-7zm0 9.5A2.5 2.5 0 1 1 12 6.5a2.5 2.5 0 0 1 0 5z"/></svg></span><span>14 Larkspur Road<br>Kelvale, WA 6999</span></div>
    <div class="info-row" style="top:330px"><span class="bubble"><svg width="18" height="18" viewBox="0 0 24 24" aria-hidden="true"><path fill="#2a2828" d="M6.6 10.8a15 15 0 0 0 6.6 6.6l2.2-2.2c.3-.3.7-.4 1-.2 1.1.4 2.3.6 3.6.6.6 0 1 .4 1 1V20c0 .6-.4 1-1 1A17 17 0 0 1 3 4c0-.6.4-1 1-1h3.5c.6 0 1 .4 1 1 0 1.3.2 2.5.6 3.6.1.3 0 .7-.2 1z"/></svg></span><span>CALL US :<br>(08) 5550 1842</span></div>
    <div class="info-row" style="top:404px"><span class="bubble"><svg width="18" height="18" viewBox="0 0 24 24" aria-hidden="true"><path fill="#2a2828" d="M3 5h18v14H3zm2 2v.5l7 5 7-5V7l-7 5z"/></svg></span><span>MAIL US :<br>info@companyname.com</span></div>
    <div class="abs footer-brand"><span class="mark"></span>Kelvale Heel Care Clinic</div>
    <div class="abs connect">Connect With Us : <div class="social"><span></span><span></span><span></span><span></span></div></div>
  </section>
  <div class="abs rule"></div>
  <p class="abs copyright">© copyright 2017 Kelvale Heel Care Clinic. All Rights Reserved &nbsp;|&nbsp; Privacy policy</p>
</footer>

</body>
</html>
```